Dental Savings Plan - Raymond Castell DDS

We need a tri-fold brochure and 1 page flyer/poster for Dr. Raymond Castell' dental office located on Maui, Hawaii. We are offering a new "Dental Savings Plan" to patients.
I have included 3 photos, along with the office logo. You do not have to use all photos if you do not want to. We want this to catch the eyes of patients, easy for them to read and understand, and to show them that this is a much better option than dental insurance.
Please use same Hawaiian theme and colors on the office website https://www.brightcoveclinic.com .

Please also include the following to promote this new plan:

Dental Services Include
• Professional Dental Cleanings (2 per benefit year)
• Perio Maintenance Cleanings (3 per benefit year) covered at 80%
• Radiographs as needed (1 set of X-rays per benefit year)
• Doctor Examinations (2 per benefit year)
• Ozone Treatment
• BRISK Amalgam Removal
• Additional limited/emergency exam (1 per benefit year)
• Cosmetic consultation
• 15% discount on all other services (including cosmetic procedures)
• 10% discount on implants and implant crowns

Advantages of the Dental Savings Plan
1. No deductibles
2. No waiting periods
3. No claims to file
4. No frequency limitations or exclusions
5. No yearly maximum benefits
6. No pre-authorization requirements
7. No pre-existing conditions limitations
8. State of the art facility and technology
9. Immediate enrollment
10. Highest quality of care for you and your Ohana

Annual Fee
$399 first family member/individual (equivalent to $33 per month)
$349 second family member (equivalent to $29 per month)
$249 each additional family member (equivalent to $20 per month)

Provisions of the Dental Savings Plan
• May not be combined with insurance plans, discounts or promotions
• This Dental Savings Plan is not an insurance plan, but a payment arrangement provided by Raymond Castell DDS, and is not transferable to any other dental office or dental specialist
• Payment for services are due at the date of service
• This program is for you and is not transferable
• Benefits are provided for one year from the date the plan is purchased
• Must be paid in full when starting the plan
• No refunds will be provided for dues of the plan annual fee under any circumstances, including failure to schedule and maintain appointments
• If Pay Ladder is used to pay for the program and for services then only a 10% discount will be given
• To receive the full 15% discount on restorative treatment, you must schedule the appointment the day it is recommended. Any failed appointment results in the loss of the 15% discount.

Target Market(s)

Dental patients without dental insurance

Industry/Entity Type

Dental Clinic

Requirements
Must have
• My project must have the logo file to identify the dental office, Hawaiian theme, same colors as website, match style of website font, theme and colors, as well as, all the Dental Services, Advantages of the Dental Savings Plan, Annual Fee, and the Provisions of the Dental Savings Plan.

```html
<!DOCTYPE html>
<html lang="en">
<head>
<meta charset="utf-8">
<title>Dental Savings Plan – Raymond Castell DDS</title>
<link href="https://fonts.googleapis.com/css2?family=Yanone+Kaffeesatz:wght@300;400;600;700&family=Open+Sans:ital,wght@0,400;0,600;0,700;1,600;1,700&display=swap" rel="stylesheet">
<style>
:root{
  --bg:#e3e3e3;
  --dark:#3b3c3d;
  --dark-deep:#2f3031;
  --blue:#27a6e1;
  --blue-deep:#1a8fc9;
  --green:#8dc63f;
  --white:#ffffff;
  --ink:#1d1d1d;
  --muted:#d8d8d8;
}
*{box-sizing:border-box;margin:0;padding:0}
html,body{width:1200px;height:923px;overflow:hidden}
body{background:var(--bg);font-family:"Open Sans",sans-serif;position:relative}
.spread{position:absolute;left:30px;width:1140px;height:430px;display:flex;box-shadow:0 6px 18px rgba(0,0,0,.25)}
.spread--outside{top:18px}
.spread--inside{top:474px}
.panel{width:380px;height:430px;position:relative;overflow:hidden}
.dark{background:var(--dark);color:var(--white)}
.blue{background:var(--blue);color:var(--white)}
.white{background:var(--white);color:var(--ink)}
.photo{display:block;width:100%}

/* outside: fee panel */
.photo--treatment{height:165px;background:linear-gradient(120deg,#f1e2dc 0%,#e9c9bd 35%,#f6f3f1 70%,#dfe6ea 100%)}
.fee{padding:22px 34px}
.fee__title{font-family:"Open Sans",sans-serif;font-style:italic;font-weight:700;font-size:28px;color:var(--blue);text-align:right;margin-bottom:14px}
.fee__item{font-style:italic;font-size:13px;line-height:1.45;margin-bottom:14px}
.fee__item b{font-size:15px}

/* outside: middle */
.photo--beach{height:262px;background:linear-gradient(180deg,#2e7fd0 0%,#6fb3ea 38%,#bfe3f4 50%,#2bb8d6 58%,#1f8fb8 80%,#7fbf6a 100%)}
.offer{height:168px;display:flex;flex-direction:column;align-items:center;justify-content:center;text-align:center;font-size:21px;line-height:1.3;font-weight:600}
.offer__plan{color:var(--green);font-style:italic;font-weight:700}

/* outside: cover */
.brand{height:150px;display:flex;align-items:center;justify-content:center;gap:12px}
.brand__dot{width:22px;height:22px;border-radius:50%;background:var(--green);flex:none}
.brand__name{font-family:"Yanone Kaffeesatz",sans-serif;font-weight:600;font-size:38px;color:var(--blue-deep);letter-spacing:.5px}
.photo--dentist{height:150px;background:linear-gradient(90deg,#eef0f2 0%,#d9dde2 40%,#9fb6c9 70%,#3d5a78 100%)}
.contact{height:130px;padding:18px 30px;font-size:12.5px}
.contact__row{display:flex;align-items:center;gap:10px;margin-bottom:8px}
.contact__row svg{width:16px;height:16px;flex:none}
.contact__pin{margin-top:8px;width:30px;height:30px;border:2px solid var(--white);display:flex;align-items:center;justify-content:center}

/* inside */
.inside-pad{padding:26px 22px 0 24px}
.heading{font-family:"Yanone Kaffeesatz",sans-serif;font-weight:600;font-size:27px;line-height:1.05;margin-bottom:12px}
.services{list-style:none;font-family:"Yanone Kaffeesatz",sans-serif;font-size:15px;line-height:1.15}
.services li{position:relative;padding-left:11px;margin-bottom:9px}
.services li::before{content:"•";position:absolute;left:0}
.services small{display:block;font-size:14px}
.advantages{list-style:none;font-family:"Yanone Kaffeesatz",sans-serif;font-size:16px}
.advantages li{margin-bottom:13px}
.advantages span{display:inline-block;width:18px}
.provisions__head{display:flex;justify-content:space-between;align-items:flex-start}
.provisions__title{color:var(--blue)}
.provisions{list-style:none;font-family:"Yanone Kaffeesatz",sans-serif;font-size:13.5px;line-height:1.12;color:var(--ink);padding-right:6px}
.provisions li{position:relative;padding-left:10px;margin-bottom:8px}
.provisions li::before{content:"•";position:absolute;left:0}
.icon-circle{position:absolute;bottom:20px;left:50%;transform:translateX(-50%)}
.corner{position:absolute;right:0;bottom:0}
</style>
</head>
<body>

<section class="spread spread--outside">
  <article class="panel dark">
    <div class="photo photo--treatment" role="img" aria-label="Photo of a patient receiving a dental check-up"></div>
    <div class="fee">
      <h2 class="fee__title">Annual Fee</h2>
      <p class="fee__item"><b>$399</b> first family member/individual<br>(equivalent to $33 per month)</p>
      <p class="fee__item"><b>$349</b> second family member<br>(equivalent to $29 per month)</p>
      <p class="fee__item"><b>$249</b> each additional family member<br>(equivalent to $20 per month)</p>
    </div>
  </article>

  <article class="panel blue">
    <div class="photo photo--beach" role="img" aria-label="Photo of a palm tree over a turquoise Hawaiian sea"></div>
    <div class="offer">
      <p>We are offering</p>
      <p>a new</p>
      <p class="offer__plan">"Dental Savings Plan"</p>
      <p>to patients</p>
    </div>
  </article>

  <article class="panel white">
    <div class="brand">
      <span class="brand__dot"></span>
      <span class="brand__name">Raymond Castell DDS</span>
    </div>
    <div class="photo photo--dentist" role="img" aria-label="Photo of the dentist in his office beside x-ray screens"></div>
    <div class="contact dark">
      <p class="contact__row"><svg viewBox="0 0 16 16"><circle cx="8" cy="8" r="7" fill="none" stroke="#fff"/><path d="M5 4.5l1.5 0 .6 2-1 .8a5 5 0 0 0 2.6 2.6l.8-1 2 .6v1.5c-3.5 .3-6.8-3-6.5-6.5z" fill="#fff"/></svg>808-555-0172</p>
      <p class="contact__row"><svg viewBox="0 0 16 16"><circle cx="8" cy="8" r="7" fill="none" stroke="#fff"/><rect x="4" y="5.5" width="8" height="5.5" fill="none" stroke="#fff"/><path d="M4 5.5l4 3 4-3" fill="none" stroke="#fff"/></svg>hello@brightcoveclinic.com</p>
      <p class="contact__row"><svg viewBox="0 0 16 16"><circle cx="8" cy="8" r="7" fill="none" stroke="#fff"/><circle cx="8" cy="8" r="4" fill="none" stroke="#fff"/><path d="M4 8h8M8 4v8" stroke="#fff"/></svg>www.brightcoveclinic.com</p>
      <p class="contact__row"><svg viewBox="0 0 16 16"><circle cx="8" cy="8" r="7" fill="none" stroke="#fff"/><path d="M8 12s-3-3.2-3-5.2a3 3 0 0 1 6 0C11 8.8 8 12 8 12z" fill="#fff"/></svg>4410 Lanai Shore Dr # 12, Kihei, HI 96700</p>
    </div>
  </article>
</section>

<section class="spread spread--inside">
  <article class="panel dark inside-pad">
    <h2 class="heading">Dental Services Include</h2>
    <ul class="services">
      <li>Professional Dental Cleanings<small>(2 per benefit year)</small></li>
      <li>Perio Maintenance Cleanings<small>(3 per benefit year) covered at 80%</small></li>
      <li>Radiographs as needed<small>(1 set of X-rays per benefit year)</small></li>
      <li>Doctor Examinations<small>(2 per benefit year)</small></li>
      <li>Ozone Treatment</li>
      <li>BRISK Amalgam Removal</li>
      <li>Additional limited/emergency exam (1 per benefit year)</li>
      <li>Cosmetic consultation</li>
      <li>15% discount on all other services (including cosmetic procedures)</li>
      <li>10% discount on implants and implant crowns</li>
    </ul>
  </article>

  <article class="panel blue inside-pad">
    <h2 class="heading">Advantages of the<br>Dental Savings Plan</h2>
    <ol class="advantages">
      <li><span>1.</span>No deductibles</li>
      <li><span>2.</span>No waiting periods</li>
      <li><span>3.</span>No claims to file</li>
      <li><span>4.</span>No frequency limitations or exclusions</li>
      <li><span>5.</span>No yearly maximum benefits</li>
      <li><span>6.</span>No pre-authorization requirements</li>
      <li><span>7.</span>No pre-existing conditions limitations</li>
      <li><span>8.</span>State of the art facility and technology</li>
      <li><span>9.</span>Immediate enrollment</li>
      <li><span>10.</span>Highest quality of care for you and your Ohana</li>
    </ol>
  </article>

  <article class="panel white inside-pad">
    <div class="provisions__head">
      <h2 class="heading provisions__title">Provisions<br>of the Dental<br>Savings Plan</h2>
      <svg width="62" height="62" viewBox="0 0 62 62" aria-hidden="true"><circle cx="31" cy="31" r="29" fill="var(--blue)"/><path d="M20 18c4-3 8-1 11 0 3-1 7-3 11 0 4 4 2 11 0 15l-2 12c-1 3-3 3-4 0l-2-8c-1-2-4-2-5 0l-2 8c-1 3-3 3-4 0l-2-12c-2-4-4-11-1-15z" fill="none" stroke="#fff" stroke-width="2"/></svg>
    </div>
    <ul class="provisions">
      <li>May not be combined with insurance plans, discounts or promotions</li>
      <li>This Dental Savings Plan is not an insurance plan, but a payment arrangement provided by Raymond Castell DDS, and is not transferable to any other dental office or dental specialist</li>
      <li>Payment for services are due at the date of service</li>
      <li>This program is for you and is not transferable</li>
      <li>Benefits are provided for one year from the date the plan is purchased</li>
      <li>Must be paid in full when starting the plan</li>
      <li>No refunds will be provided for dues of the plan annual fee under any circumstances, including failure to schedule and maintain appointments</li>
      <li>If Pay Ladder is used to pay for the program and for services then only a 10% discount will be given</li>
      <li>To receive the full 15% discount on restorative treatment, you must schedule the appointment the day it is recommended. Any failed appointment results in the loss of the 15% discount.</li>
    </ul>
    <svg class="corner" width="120" height="40" viewBox="0 0 120 40" aria-hidden="true"><path d="M0 40C40 30 80 18 120 0v40z" fill="var(--dark)"/></svg>
  </article>
</section>

</body>
</html>
```